Creative, fresh business card design for Ripplecraft Facades

We need a fresh, creative business card design for Ripplecraft Facades. We are the manufacturer of Ripplecraft Facades in Australia. Wall panels are 2400 x 1200mm panels made from MDF and feature 3D patterns on the face of the panel. The colours to be used are green, silver/grey and white RGB
Red 187
Green 207
Blue 65.

An idea is to possibly use a watermark of one of our designs as a background (like on the "Grids" design on the left hand side of page 2 of our brochure).

Target Market(s)

Interior designers, architects, builders and home renovators

Industry/Entity Type

Business

Contact Information for Business Card

Details to go on the card are:
Our logo (attached),
Slogan: "Decorative panels for interiors and exteriors",
Contact name,
Position,
Mobile phone number,
Business address,
Business phone,
Business fax,
Website and
Email address.

I have attached a few images of our panels and our brochure for reference.

The colours of the business card should feature our logo colours which are: RGB
Red 187
Green 207
Blue 65

Requirements
Must have
• Very modern fonts and design. Some of the designs shown especially the "Prisms" design which is a popular design.
Nice to have
• Creative but simple design. Very contemporary.
Should not have
• Anything ornate or old fashioned.

```html
<!DOCTYPE html>
<html lang="en">
<head>
<meta charset="utf-8">
<title>Ripplecraft Facades – Business Card</title>
<link rel="stylesheet" href="https://fonts.googleapis.com/css2?family=Open+Sans:wght@300;400;700&display=swap">
<style>
  :root {
    --brand-green: rgb(187, 207, 65);
    --stage-dark: #1f1f1f;
    --stage-light: #383838;
    --card-base: #232323;
    --band-dark: #161616;
    --text-light: #d6d6d6;
    --text-muted: #a4a4a4;
    --divider: #8f8f8f;
  }
  * { box-sizing: border-box; margin: 0; padding: 0; }
  html, body {
    width: 1200px; height: 1000px; overflow: hidden;
    font-family: "Open Sans", Arial, sans-serif;
  }
  body {
    background: radial-gradient(ellipse at 50% 30%, var(--stage-light), var(--stage-dark) 75%);
    display: flex; align-items: center; justify-content: center;
  }
  .business-card {
    position: relative;
    width: 860px; height: 490px;
    background: var(--card-base);
    overflow: hidden;
    box-shadow: 0 20px 44px rgba(0,0,0,0.6);
  }
  .watermark-top {
    position: absolute; left: 0; right: 0; top: 0; height: 180px;
    background:
      radial-gradient(ellipse 380px 220px at 0% 100%, rgba(235,235,235,0.55), rgba(235,235,235,0) 70%),
      repeating-linear-gradient(90deg, rgba(255,255,255,0.06) 0 34px, rgba(0,0,0,0.08) 34px 68px),
      repeating-linear-gradient(0deg, rgba(255,255,255,0.05) 0 30px, rgba(0,0,0,0.07) 30px 60px),
      linear-gradient(100deg, #7a7a7a 0%, #4e4e4e 30%, #333 60%, #262626 100%);
  }
  .watermark-bottom {
    position: absolute; left: 0; right: 0; top: 330px; bottom: 0;
    background:
      repeating-linear-gradient(90deg, rgba(255,255,255,0.03) 0 34px, rgba(0,0,0,0.06) 34px 68px),
      repeating-linear-gradient(0deg, rgba(255,255,255,0.03) 0 30px, rgba(0,0,0,0.05) 30px 60px),
      linear-gradient(180deg, #2a2a2a, #222 60%, #1e1e1e);
  }
  .info-band {
    position: absolute; left: 0; right: 0;
    top: 180px; height: 150px;
    background: linear-gradient(90deg, #1c1c1c, var(--band-dark) 45%, #1a1a1a);
    box-shadow: 0 0 18px rgba(0,0,0,0.45);
    display: flex; align-items: center;
    padding: 0 40px;
  }
  .brand-block { width: 300px; }
  .brand-name {
    display: flex; align-items: center; gap: 10px;
    color: var(--brand-green);
    font-weight: 700; font-size: 21px; line-height: 1.1; white-space: nowrap;
  }
  .brand-square { width: 24px; height: 24px; background: var(--brand-green); flex: none; }
  .brand-slogan {
    margin-top: 10px;
    color: var(--text-muted);
    font-size: 12px; letter-spacing: 2px; line-height: 1.4;
  }
  .person-block { width: 230px; text-align: right; padding-right: 22px; }
  .person-name {
    color: var(--brand-green); font-family: Arial, "Open Sans", sans-serif;
    font-weight: 700; font-size: 25px; line-height: 1.1;
  }
  .person-role { color: var(--text-light); font-size: 14px; margin-bottom: 14px; }
  .person-address { color: var(--text-muted); font-weight: 300; font-size: 15px; line-height: 1.4; }
  .divider { width: 1px; height: 112px; background: var(--divider); }
  .contact-list {
    list-style: none; padding-left: 22px;
    color: var(--text-light); font-weight: 300; font-size: 15px;
  }
  .contact-list li { display: flex; align-items: center; gap: 14px; line-height: 23px; white-space: nowrap; }
  .contact-list svg { width: 14px; height: 14px; flex: none; }
  .web-highlight { color: var(--brand-green); }
</style>
</head>
<body>
  <article class="business-card">
    <div class="watermark-top" role="img" aria-label="Repeated embossed panel-pattern watermark, silver fading to charcoal"></div>
    <div class="watermark-bottom" role="img" aria-label="Repeated blind-embossed panel-pattern watermark on dark card"></div>

    <section class="info-band">
      <div class="brand-block">
        <div class="brand-name"><span class="brand-square"></span>Ripplecraft Facades</div>
        <p class="brand-slogan">decorative panels for<br>interiors &amp; exteriors</p>
      </div>

      <div class="person-block">
        <h1 class="person-name">Daniel Hart</h1>
        <p class="person-role">Director</p>
        <p class="person-address">Your Street Address<br>Harbour City, 1234</p>
      </div>

      <div class="divider"></div>

      <ul class="contact-list">
        <li>
          <svg viewBox="0 0 14 14" fill="none" stroke="rgb(187,207,65)" stroke-width="1.4"><rect x="4" y="1" width="6" height="12" rx="1"/><line x1="6" y1="11" x2="8" y2="11"/></svg>
          +000 123 456 789
        </li>
        <li>
          <svg viewBox="0 0 14 14" fill="rgb(187,207,65)"><path d="M3 1l2 3-1.2 1.4c.8 1.8 2 3 3.8 3.8L9 8l3 2-1 2.5C6 12.5 1.5 8 1.5 3z"/></svg>
          +000 123 456 789
        </li>
        <li>
          <svg viewBox="0 0 14 14" fill="rgb(187,207,65)"><rect x="4" y="1" width="6" height="4"/><rect x="1" y="5" width="12" height="6" rx="1"/><rect x="4" y="9" width="6" height="4" fill="#161616" stroke="rgb(187,207,65)"/></svg>
          +000 123 456 789
        </li>
        <li>
          <svg viewBox="0 0 14 14" fill="rgb(187,207,65)"><rect x="1" y="3" width="12" height="8"/><path d="M1 3l6 5 6-5" fill="none" stroke="#161616" stroke-width="1.2"/></svg>
          yourname@email.com
        </li>
        <li>
          <svg viewBox="0 0 14 14" fill="none" stroke="rgb(187,207,65)" stroke-width="1.8"><circle cx="8" cy="6" r="4"/><line x1="5" y1="9" x2="1.5" y2="12.5"/></svg>
          <span>www.<span class="web-highlight">websitename</span>.com</span>
        </li>
      </ul>
    </section>
  </article>
</body>
</html>
```